BrivoTerna. Lantern of the Steady Harvest. Business card

Professional business card for BrivoTerna (Lantern of the Steady Harvest)
My rationale: Strategy-> Execution-> Results-> Value that lead to the BrivoTerna name: We put the Lantern of the Steady Harvest.
We deliver value to our customers helping them at defining a good strategy (cyan arrow). 90% of well formulated strategies fail due to poor execution so we also consider strategical execution very important (green arrow). Due to the execution we obtain the results (blue arrow). Finally, the results provide feedback to redefine strategy, and the new strategy has to be executed and new results obtained providing new feedback and on and on. It's like a wheel that finally, must create corporate value: value for shareholders, staholders, employees, providers...-

Target Market(s)

CEOs and steering comitees , invewrnent funds

Industry/Entity Type

Business Consultant

Contact Information for Business Card

Teodoro Vinsquel
CEO & Founder
teodoro.vinsquel@brivoterna-example.com
Mobile: +34 655.803.912
www.brivoterna-example.com

Colors

Designer to choose colors to be used in the design.

Requirements
Nice to have
• Nice to hace the words: Strategy, execution, results
• Nice to vave the claim: Lantern of the Steady Harvest
• The three colors should be shown:
• cyan for STRATEGY
• green for EXECUTION
• blue for RESULTS
Should not have
• Complete black background

```html
<!DOCTYPE html>
<html lang="en">
<head>
<meta charset="utf-8">
<title>BrivoTerna – Business Card</title>
<link href="https://fonts.googleapis.com/css2?family=Roboto:wght@300;400;700;900&display=swap" rel="stylesheet">
<style>
  :root {
    --navy: #0a3399;
    --cyan: #12a9e6;
    --green: #8dc63f;
    --white: #ffffff;
    --ink: #1f3c8f;
    --stage: #3a3a3d;
    --faint: #eef2f9;
  }
  * { box-sizing: border-box; margin: 0; padding: 0; }
  html, body {
    width: 1200px; height: 880px; overflow: hidden;
    background: var(--stage);
    font-family: "Roboto", Arial, sans-serif;
  }
  .canvas { position: relative; width: 1200px; height: 880px; }

  .card {
    position: absolute;
    width: 560px; height: 320px;
    border-radius: 18px;
    overflow: hidden;
    box-shadow: 0 14px 30px rgba(0,0,0,0.35);
  }

  /* Back side */
  .card-back {
    left: 80px; top: 90px;
    background: var(--navy);
    display: flex; align-items: center; justify-content: center;
  }
  .card-back .brand-name {
    color: var(--white);
    font-weight: 900;
    font-size: 46px;
    letter-spacing: -0.5px;
  }

  /* Front side */
  .card-front {
    left: 560px; top: 470px;
    background: var(--white);
  }
  .faint-mark {
    position: absolute; right: -40px; top: -30px;
    width: 300px; height: 300px; border-radius: 50%;
    background: var(--faint);
  }
  .front-content { position: absolute; left: 38px; top: 54px; }
  .front-content .brand-name {
    color: var(--navy);
    font-weight: 900;
    font-size: 44px;
    letter-spacing: -0.5px;
    line-height: 1;
  }
  .person { margin-top: 26px; }
  .person-name { color: var(--cyan); font-weight: 700; font-size: 21px; }
  .person-title { color: var(--ink); font-weight: 300; font-size: 15px; margin-top: 2px; }
  .contacts { list-style: none; margin-top: 18px; }
  .contacts li {
    display: flex; align-items: center; gap: 9px;
    color: var(--ink); font-weight: 300; font-size: 14px;
    margin-bottom: 5px;
  }
  .contacts svg { width: 13px; height: 13px; fill: var(--cyan); flex: none; }

  .edge-band { position: absolute; left: 0; right: 0; bottom: 0; height: 10px; display: flex; }
  .edge-band .strategy { width: 22%; background: var(--cyan); }
  .edge-band .gap { width: 6px; background: var(--white); }
  .edge-band .results { flex: 1; background: var(--navy); }
</style>
</head>
<body>
<div class="canvas">

  <section class="card card-back">
    <span class="brand-name">BrivoTerna</span>
  </section>

  <section class="card card-front">
    <div class="faint-mark" role="img" aria-label="Faint brand decoration"></div>
    <div class="front-content">
      <div class="brand-name">BrivoTerna</div>
      <div class="person">
        <div class="person-name">Teodoro Vinsquel</div>
        <div class="person-title">CEO &amp; Founder</div>
      </div>
      <ul class="contacts">
        <li>
          <svg viewBox="0 0 24 24" aria-hidden="true"><path d="M6.6 10.8a15.1 15.1 0 0 0 6.6 6.6l2.2-2.2c.3-.3.7-.4 1-.2 1.1.4 2.3.6 3.6.6.6 0 1 .4 1 1V20c0 .6-.4 1-1 1A17 17 0 0 1 3 4c0-.6.4-1 1-1h3.5c.6 0 1 .4 1 1 0 1.3.2 2.5.6 3.6.1.3 0 .7-.2 1z"/></svg>
          +34 655.803.912
        </li>
        <li>
          <svg viewBox="0 0 24 24" aria-hidden="true"><path d="M12 2a10 10 0 1 0 0 20 10 10 0 0 0 0-20zm6.9 6h-3a15.7 15.7 0 0 0-1.4-3.6A8 8 0 0 1 18.9 8zM12 4c.8 1.2 1.5 2.5 1.9 4h-3.8c.4-1.5 1.1-2.8 1.9-4zM4.3 14a8 8 0 0 1 0-4h3.4a16 16 0 0 0 0 4zm.8 2h3a15.7 15.7 0 0 0 1.4 3.6A8 8 0 0 1 5.1 16zm3-8h-3a8 8 0 0 1 4.4-3.6C8.9 5.5 8.4 6.7 8.1 8zM12 20c-.8-1.2-1.5-2.5-1.9-4h3.8c-.4 1.5-1.1 2.8-1.9 4zm2.3-6H9.7a14.7 14.7 0 0 1 0-4h4.6a14.7 14.7 0 0 1 0 4zm.2 5.6c.6-1.1 1.1-2.3 1.4-3.6h3a8 8 0 0 1-4.4 3.6zm1.8-5.6a16 16 0 0 0 0-4h3.4a8 8 0 0 1 0 4z"/></svg>
          www.brivoterna-example.com
        </li>
        <li>
          <svg viewBox="0 0 24 24" aria-hidden="true"><path d="M2 5h20v14H2zm2 2v.5l8 5 8-5V7l-8 5z"/></svg>
          teodoro.vinsquel@brivoterna-example.com
        </li>
      </ul>
    </div>
    <div class="edge-band">
      <span class="strategy"></span><span class="gap"></span><span class="results"></span>
    </div>
  </section>

</div>
</body>
</html>
```